Business card for a new cabinet shop company named Veloran Cabinets for high end cabinets

Design a business card, thinking dark rich green with colours to speak of high end luxury ie; cream, gold, black possibly

Mitchell Tarrowby
Director Craftsman
Email: info@veloranjoinery-example.com.au
Instagram : @veloran.cabinets

```html
<!DOCTYPE html>
<html lang="en">
<head>
<meta charset="utf-8">
<title>Veloran Cabinets — Business Card</title>
<link rel="stylesheet" href="https://fonts.googleapis.com/css2?family=Montserrat:wght@400;500;700&display=swap">
<style>
  :root {
    --backdrop: #2b2b2b;
    --card-green: #1f3d3a;
    --pattern-light: #25504b;
    --pattern-dark: #1c3835;
    --gold: #c9a55e;
    --cream: #f3efe6;
    --rule: #e8e4da;
  }
  html, body {
    margin: 0;
    padding: 0;
    width: 1200px;
    height: 694px;
    overflow: hidden;
    background: var(--backdrop);
    font-family: "Montserrat", sans-serif;
  }
  .canvas {
    position: relative;
    width: 1200px;
    height: 694px;
    display: flex;
    align-items: center;
    justify-content: center;
    gap: 40px;
  }
  .card {
    position: relative;
    width: 540px;
    height: 318px;
    border-radius: 22px;
    background: var(--card-green);
    overflow: hidden;
    box-shadow: 0 18px 40px rgba(0,0,0,0.45);
  }

  /* Back of card */
  .card-back__pattern {
    position: absolute;
    inset: 0;
    background: linear-gradient(135deg, var(--pattern-light) 0%, var(--card-green) 55%, var(--pattern-dark) 100%);
  }
  .card-back__brand {
    position: absolute;
    left: 0;
    right: 0;
    top: 50%;
    transform: translateY(-50%);
    text-align: center;
    color: var(--gold);
    font-weight: 500;
    font-size: 30px;
    letter-spacing: 0.04em;
  }

  /* Front of card */
  .brand {
    position: absolute;
    top: 48px;
    right: 40px;
    display: flex;
    align-items: center;
    gap: 14px;
  }
  .brand__mark {
    width: 14px;
    height: 14px;
    border-radius: 50%;
    background: var(--gold);
  }
  .brand__name {
    color: var(--gold);
    font-weight: 500;
    font-size: 30px;
    letter-spacing: 0.04em;
  }
  .divider {
    position: absolute;
    left: 40px;
    right: 40px;
    top: 168px;
    height: 1px;
    background: var(--rule);
    opacity: 0.85;
  }
  .person {
    position: absolute;
    left: 40px;
    top: 110px;
  }
  .person__name {
    margin: 0;
    color: var(--gold);
    font-weight: 700;
    font-size: 24px;
    line-height: 1.1;
  }
  .person__title {
    margin: 4px 0 0;
    color: var(--cream);
    font-weight: 400;
    font-size: 14px;
    letter-spacing: 0.02em;
  }
  .contact {
    position: absolute;
    left: 40px;
    top: 190px;
    margin: 0;
    padding: 0;
    list-style: none;
  }
  .contact__item {
    display: flex;
    align-items: center;
    gap: 10px;
    color: var(--cream);
    font-size: 13px;
    margin-bottom: 10px;
  }
  .contact__icon {
    width: 14px;
    height: 14px;
    flex: none;
  }
  .social {
    position: absolute;
    right: 40px;
    bottom: 36px;
    display: flex;
    align-items: center;
    gap: 8px;
    color: var(--cream);
    font-size: 13px;
  }
  .social__mark {
    width: 11px;
    height: 11px;
    border: 1.5px solid var(--gold);
    border-radius: 3px;
  }
</style>
</head>
<body>
<main class="canvas">

  <section class="card card-back" aria-label="Card back">
    <div class="card-back__pattern" role="img" aria-label="Embossed tonal repeat pattern across the card back"></div>
    <div class="card-back__brand">Veloran Cabinets</div>
  </section>

  <section class="card card-front" aria-label="Card front">
    <div class="brand">
      <span class="brand__mark"></span>
      <span class="brand__name">Veloran Cabinets</span>
    </div>

    <div class="person">
      <h1 class="person__name">Mitchell Tarrowby</h1>
      <p class="person__title">Director Craftsman</p>
    </div>

    <div class="divider"></div>

    <ul class="contact">
      <li class="contact__item">
        <svg class="contact__icon" viewBox="0 0 16 16" aria-hidden="true">
          <rect x="1" y="3" width="14" height="10" rx="1" fill="var(--gold)"/>
          <path d="M1.5 3.5 L8 9 L14.5 3.5" fill="none" stroke="var(--card-green)" stroke-width="1.4"/>
        </svg>
        <span>info@veloranjoinery-example.com.au</span>
      </li>
      <li class="contact__item">
        <svg class="contact__icon" viewBox="0 0 16 16" aria-hidden="true">
          <path d="M8 1 C4.7 1 2.5 3.3 2.5 6.2 C2.5 10 8 15 8 15 C8 15 13.5 10 13.5 6.2 C13.5 3.3 11.3 1 8 1 Z" fill="var(--gold)"/>
          <circle cx="8" cy="6.2" r="2" fill="var(--card-green)"/>
        </svg>
        <span>Western Australia</span>
      </li>
    </ul>

    <div class="social">
      <span class="social__mark"></span>
      <span>@veloran.cabinets</span>
    </div>
  </section>

</main>
</body>
</html>
```